1876 Basins & Spouts Business Card

I'm wanting to get a business card designed. Our business is 1876 Basins & Spouts
Details for the card:

1876 Basins & Spouts
Name: Harold Vesk
Email: harold@1876basinsandspouts.com.au
Website: www.1876basinsandspouts.com.au
Mobile: 0438 260 947
Phone: 02 7481 3926

Font of Basins & Spouts is called Snell Roundhand. Not sue what font logo text is.

I'm thinking two sided but it doesn't have to be.

```html
<!DOCTYPE html>
<html lang="en">
<head>
<meta charset="utf-8">
<title>1876 Basins &amp; Spouts — Business Card</title>
<link href="https://fonts.googleapis.com/css2?family=Lato:wght@400&family=Montserrat:wght@500&display=swap" rel="stylesheet">
<style>
  :root {
    --backdrop: #2b2b2b;
    --card-white: #ffffff;
    --ink: #1e1e1e;
    --ink-soft: #333333;
    --ink-muted: #6a6a6a;
    --rule: #3a3a3a;
    --back-frame: #8c8c8c;
    --tile-light: #c9c9c7;
    --tile-mid: #a9a8a5;
    --tile-warm: #b3a592;
    --tile-blue: #8d95ad;
    --on-photo: #ffffff;
  }
  * { box-sizing: border-box; margin: 0; padding: 0; }
  html, body {
    width: 1200px; height: 900px; overflow: hidden;
    background: var(--backdrop);
  }
  .card {
    position: absolute; left: 261px; width: 656px; height: 358px;
  }
  .card-front {
    top: 69px; background: var(--card-white);
    font-family: 'Lato', sans-serif; color: var(--ink-soft);
  }
  .brand {
    position: absolute; left: 34px; top: 162px; width: 245px;
  }
  .brand-name {
    font-family: 'Lato', sans-serif; font-size: 20px; color: var(--ink);
    white-space: nowrap; line-height: 1.2;
  }
  .brand-tagline {
    font-family: 'Lato', sans-serif; font-size: 7px; color: var(--ink-muted);
    margin-top: 5px; letter-spacing: 0.2px; white-space: nowrap;
  }
  .divider {
    position: absolute; left: 296px; top: 85px; width: 1.5px; height: 191px;
    background: var(--rule);
  }
  .details { position: absolute; left: 319px; top: 80px; }
  .person-name {
    font-family: 'Montserrat', sans-serif; font-weight: 500;
    font-size: 29px; letter-spacing: 2.2px; color: var(--ink); line-height: 1;
  }
  .person-role { font-size: 15.5px; letter-spacing: 0.8px; margin-top: 3px; }
  .address { font-size: 15.5px; letter-spacing: 0.9px; line-height: 21px; margin-top: 12px; }
  .contacts { list-style: none; margin-top: 11px; }
  .contacts li {
    display: flex; align-items: center; font-size: 15.5px; letter-spacing: 1px;
    height: 21.3px; white-space: nowrap;
  }
  .contacts svg { width: 12px; height: 12px; margin-right: 8px; flex: none; }

  .card-back {
    top: 472px; background: var(--back-frame); padding: 5px 6px;
    display: grid;
    grid-template-columns: 129px 177px 177px 132px;
    grid-template-rows: 169px 168px;
    column-gap: 10px; row-gap: 10px;
  }
  .photo-tile { display: block; }
  .tile-light { background: linear-gradient(160deg, var(--tile-light), var(--tile-mid)); }
  .tile-warm { background: linear-gradient(170deg, var(--tile-light), var(--tile-warm)); }
  .tile-blue { background: linear-gradient(180deg, var(--tile-light) 45%, var(--tile-blue)); }
  .back-name {
    position: absolute; left: 0; right: 0; top: 162px; text-align: center;
    font-family: 'Lato', sans-serif; font-size: 26px; color: var(--on-photo);
  }
</style>
</head>
<body>
  <section class="card card-front">
    <div class="brand">
      <div class="brand-name">1876 Basins &amp; Spouts</div>
      <div class="brand-tagline">Enduring elegance paired with effortless everyday use</div>
    </div>
    <div class="divider"></div>
    <div class="details">
      <h1 class="person-name">HAROLD VESK</h1>
      <p class="person-role">Director</p>
      <p class="address">PO Box 48 Mount<br>Tallow NSW 2793</p>
      <ul class="contacts">
        <li>
          <svg viewBox="0 0 12 12" fill="none" stroke="#222" stroke-width="1.2"><path d="M3 1 L4.5 3.5 L3.5 4.5 C4 6.5 5.5 8 7.5 8.5 L8.5 7.5 L11 9 L10 11 C5 11 1 7 1 2 Z"/></svg>
          0438 260 947
        </li>
        <li>
          <svg viewBox="0 0 12 12" fill="none" stroke="#222" stroke-width="1.3"><rect x="3" y="0.8" width="6" height="10.4" rx="1"/><line x1="5" y1="9.3" x2="7" y2="9.3"/></svg>
          02 7481 3926
        </li>
        <li>
          <svg viewBox="0 0 12 12" fill="none" stroke="#222" stroke-width="1.2"><rect x="0.8" y="2.5" width="10.4" height="7" rx="0.8"/><path d="M1 3 L6 6.5 L11 3"/></svg>
          harold@1876basinsandspouts.com.au
        </li>
        <li>
          <svg viewBox="0 0 12 12" fill="none" stroke="#222" stroke-width="1"><circle cx="6" cy="6" r="5.2"/><ellipse cx="6" cy="6" rx="2.3" ry="5.2"/><line x1="0.8" y1="6" x2="11.2" y2="6"/><line x1="1.6" y1="3.5" x2="10.4" y2="3.5"/><line x1="1.6" y1="8.5" x2="10.4" y2="8.5"/></svg>
          www.1876basinsandspouts.com.au
        </li>
      </ul>
    </div>
  </section>

  <section class="card card-back">
    <div class="photo-tile tile-light" role="img" aria-label="White kitchen corner with gas cooktop and oven"></div>
    <div class="photo-tile tile-warm" role="img" aria-label="Dining table with copper pendant lights and autumn branches in a vase"></div>
    <div class="photo-tile tile-light" role="img" aria-label="Laundry with farmhouse sink, timber benchtop and washing machine"></div>
    <div class="photo-tile tile-light" role="img" aria-label="Window-lit kitchen sink with tiled splashback"></div>
    <div class="photo-tile tile-warm" role="img" aria-label="White kitchen island with metal bar stools"></div>
    <div class="photo-tile tile-light" role="img" aria-label="Kitchen with open shelving, patterned splashback and oven"></div>
    <div class="photo-tile tile-blue" role="img" aria-label="Brass bridge tap above blue hydrangeas"></div>
    <div class="photo-tile tile-light" role="img" aria-label="Brass tap running into a white basin beside a vase of flowers"></div>
    <div class="back-name">1876 Basins &amp; Spouts</div>
  </section>
</body>
</html>
```